Business Card Design

WE are looking for a premium quality Business Cards for a Law Firm . Copies of our current business card is attached.

Contact Information for Business Card

xyz

```html
<!DOCTYPE html>
<html lang="en">
<head>
<meta charset="utf-8">
<title>Ashbury Lawyers – Business Card</title>
<link rel="stylesheet" href="https://fonts.googleapis.com/css2?family=Cinzel:wght@700&family=Arimo:wght@400;700&display=swap">
<style>
  :root {
    --stage: #141414;
    --card: #2a2a2a;
    --card-deep: #222222;
    --gold: #c9a050;
    --white: #f4f4f4;
    --muted: #3a3a3a;
  }
  * { box-sizing: border-box; margin: 0; padding: 0; }
  html, body { width: 1200px; height: 963px; overflow: hidden; background: var(--stage); }
  body {
    display: flex; flex-direction: column; align-items: center; justify-content: center; gap: 56px;
    font-family: "Arimo", Arial, sans-serif; color: var(--white);
  }
  .card {
    position: relative; width: 640px; height: 391px;
    background: linear-gradient(160deg, var(--card) 0%, var(--card-deep) 100%);
    border-radius: 22px;
    border-bottom: 3px solid var(--gold);
    overflow: hidden;
  }
  .brand { display: flex; align-items: center; gap: 16px; }
  .brand-ring { width: 74px; height: 74px; border: 4px solid var(--gold); border-radius: 50%; flex: none; }
  .brand-name { font-family: "Cinzel", Georgia, serif; font-weight: 700; color: var(--white); line-height: 1; letter-spacing: 1px; }

  .card-front .brand { position: absolute; top: 56px; left: 190px; }
  .card-front .brand-name { font-size: 36px; }

  .details { position: absolute; top: 190px; left: 0; right: 0; display: flex; justify-content: center; }
  .person { text-align: right; padding-right: 22px; border-right: 1px solid var(--white); }
  .person-name { color: var(--gold); font-weight: 700; font-size: 19px; margin-bottom: 6px; }
  .person-role { font-size: 12.5px; text-transform: uppercase; margin-bottom: 5px; }
  .person-quals { font-size: 12.5px; }
  .contact { list-style: none; padding-left: 22px; font-size: 13.5px; }
  .contact li { display: flex; align-items: center; gap: 10px; margin-bottom: 6px; }
  .contact svg { width: 14px; height: 14px; flex: none; }
  .address { position: absolute; bottom: 54px; left: 0; right: 0; text-align: center; font-size: 13.5px; }

  .card-back .emblem-area {
    position: absolute; top: 30px; left: 60px; width: 300px; height: 300px; border-radius: 50%;
    border: 10px solid #1c1c1c; background: radial-gradient(circle at 40% 35%, #303030, #232323);
  }
  .card-back .brand { position: absolute; right: 48px; bottom: 48px; }
  .card-back .brand-name { font-size: 34px; }
</style>
</head>
<body>
  <section class="card card-front" aria-label="Business card front">
    <div class="brand">
      <span class="brand-ring"></span>
      <span class="brand-name">ASHBURY LAWYERS</span>
    </div>
    <div class="details">
      <div class="person">
        <p class="person-name">DANIEL MOREAU</p>
        <p class="person-role">Director &amp; Principal Solicitor</p>
        <p class="person-quals">MBA, Juris Doctor</p>
      </div>
      <ul class="contact">
        <li><svg viewBox="0 0 24 24" fill="none" stroke="var(--gold)" stroke-width="2"><path d="M5 3h4l2 5-2.5 1.5a11 11 0 0 0 6 6L16 13l5 2v4a2 2 0 0 1-2 2A16 16 0 0 1 3 5a2 2 0 0 1 2-2z"/></svg>+61 7 3000 1234</li>
        <li><svg viewBox="0 0 24 24" fill="none" stroke="var(--gold)" stroke-width="2"><rect x="7" y="2" width="10" height="20" rx="2"/><path d="M11 18h2"/></svg>+61 0400 123 456</li>
        <li><svg viewBox="0 0 24 24" fill="none" stroke="var(--gold)" stroke-width="2"><rect x="3" y="5" width="18" height="14" rx="1"/><path d="M3 6l9 7 9-7"/></svg>daniel@ashburylawyers.com.au</li>
        <li><svg viewBox="0 0 24 24" fill="none" stroke="var(--gold)" stroke-width="2"><circle cx="12" cy="12" r="9"/><path d="M3 12h18M12 3c3 3 3 15 0 18M12 3c-3 3-3 15 0 18"/></svg>www.ashburylawyers.com.au</li>
      </ul>
    </div>
    <p class="address">Level 3, Ashbury House, 120 Harbour Street, Fairview, QLD 4000</p>
  </section>

  <section class="card card-back" aria-label="Business card back">
    <div class="emblem-area" role="img" aria-label="Large embossed firm emblem area"></div>
    <div class="brand">
      <span class="brand-name">ASHBURY LAWYERS</span>
    </div>
  </section>
</body>
</html>
```